CONTEMPORARY Canva Art Design for Christians

I need a canvas art design on Christianity. The design must be in 3 SIMPLE dimensions: 12x 18 inches / 28 x 24 inches / 30 x 40 inches
The design must be accompanied by christian quote.
The christian quote can be "As For Me And My House We Will Serve The Lord (Joshua 24:15)" or any other quote that is good for display in a christian home.

I DON'T WANT THE TRADITIONAL CHRISTIAN DESIGN.. I WANT COLOURFUL, MEANINGFUL and CONTEMPORARY, MODERN DESIGN. And stay away from the scary image of Jesus in dark background, it only makes the home more scary not holy!

Target Market(s)

Christians

Colors

Designer to choose colors to be used in the design.

Requirements
Must have
• A graphic design and a christian quote that is powerful and edifies the soul. Great for display at home. Great use of colours to enhance the message.
Nice to have
• I wish to see great unique design with strong use of colours, images to enhance the scripture. It must glorify Jesus.
Should not have
• Should not be dull.

```html
<!DOCTYPE html>
<html lang="en">
<head>
<meta charset="utf-8">
<title>As For Me And My House – Canvas Art</title>
<link href="https://fonts.googleapis.com/css2?family=Roboto+Condensed:wght@300;400&display=swap" rel="stylesheet">
<style>
  :root {
    --page-bg: #e9e9ea;
    --sky-top: #241c5e;
    --sky-mid: #4f36a0;
    --sky-violet: #9a66c8;
    --sky-glow: #f4dbe8;
    --horizon: #f59a3a;
    --ground: #0e0908;
    --sun: #ffd66a;
    --cross-light: #ffffff;
    --ink: #111014;
  }
  html, body {
    margin: 0;
    padding: 0;
    width: 1200px;
    height: 1200px;
    overflow: hidden;
    background: var(--page-bg);
  }
  .canvas-art {
    position: absolute;
    left: 0;
    top: 200px;
    width: 1200px;
    height: 800px;
    display: block;
  }
  .verse-line {
    font-family: "Roboto Condensed", "Arial Narrow", sans-serif;
    font-weight: 300;
    font-size: 79px;
    fill: var(--ink);
    letter-spacing: -1px;
  }
  .verse-reference {
    font-family: "Roboto Condensed", "Arial Narrow", sans-serif;
    font-weight: 300;
    font-size: 34px;
    fill: var(--ink);
  }
</style>
</head>
<body>
<svg class="canvas-art" viewBox="0 0 1200 800" xmlns="http://www.w3.org/2000/svg">
  <defs>
    <linearGradient id="skyGradient" x1="0" y1="0" x2="0" y2="1">
      <stop offset="0" stop-color="var(--sky-top)"/>
      <stop offset="0.35" stop-color="var(--sky-mid)"/>
      <stop offset="0.6" stop-color="var(--sky-violet)"/>
      <stop offset="0.76" stop-color="var(--sky-glow)"/>
      <stop offset="0.85" stop-color="var(--horizon)"/>
      <stop offset="0.89" stop-color="var(--ground)"/>
      <stop offset="1" stop-color="var(--ground)"/>
    </linearGradient>
    <radialGradient id="sunGlow" cx="0.5" cy="0.5" r="0.5">
      <stop offset="0" stop-color="var(--sun)" stop-opacity="0.95"/>
      <stop offset="0.45" stop-color="var(--horizon)" stop-opacity="0.5"/>
      <stop offset="1" stop-color="var(--horizon)" stop-opacity="0"/>
    </radialGradient>
    <radialGradient id="crossHalo" cx="0.5" cy="0.5" r="0.5">
      <stop offset="0" stop-color="var(--cross-light)" stop-opacity="0.45"/>
      <stop offset="1" stop-color="var(--cross-light)" stop-opacity="0"/>
    </radialGradient>
    <filter id="softBlur" x="-20%" y="-20%" width="140%" height="140%">
      <feGaussianBlur stdDeviation="6"/>
    </filter>
  </defs>

  <rect class="scene-photo" x="0" y="0" width="1200" height="800" fill="url(#skyGradient)"
        role="img" aria-label="Photo: family silhouettes forming a roof with their arms against a purple and orange sunset over a grassy meadow"/>
  <ellipse class="sun-glow" cx="870" cy="690" rx="300" ry="140" fill="url(#sunGlow)"/>

  <g class="glowing-cross">
    <circle cx="889" cy="180" r="190" fill="url(#crossHalo)"/>
    <g filter="url(#softBlur)" fill="var(--cross-light)" fill-opacity="0.55">
      <rect x="863" y="66" width="52" height="205"/>
      <rect x="749" y="165" width="281" height="47"/>
    </g>
  </g>

  <g class="verse" text-anchor="middle">
    <text class="verse-line" x="875" y="333">AS FOR ME AND</text>
    <text class="verse-line" x="875" y="416">MY HOUSE</text>
    <text class="verse-line" x="875" y="500">WE WILL SERVE</text>
    <text class="verse-line" x="875" y="584">THE LORD</text>
    <text class="verse-reference" x="875" y="631">(JOSHUA 24:15)</text>
  </g>
</svg>
</body>
</html>
```